Business Card Design Project

I require a business card with the following information on them for various different people;
name
m:
f:
e:
I have a logo already and will attached that. We are in the construction industry. I require something clean and simple but eye catching at the same time. You can use another colour with our logo if you like and you can style the logo as well if you wish. I am open.
Also it needs to be front and back design.
Industry/Entity Type
Construction
Requirements
Must have
- Logo, name, mobile, fax and email address.
Front and back design

```html
<!DOCTYPE html>
<html lang="en">
<head>
<meta charset="utf-8">
<title>Stoneford Builders – Business Cards</title>
<link rel="stylesheet" href="https://fonts.googleapis.com/css2?family=Open+Sans:wght@400;700&display=swap">
<style>
  :root {
    --backdrop: #e8e5e0;
    --card-white: #ffffff;
    --card-grey-light: #f3f3f3;
    --card-grey-dark: #c9cacc;
    --brand-green: #5aab3c;
    --brand-green-light: #a9d25a;
    --ink: #4a4a4a;
    --ink-soft: #5c5c5c;
    --card-shadow: 0 1px 3px rgba(0,0,0,.25);
  }
  * { margin: 0; padding: 0; box-sizing: border-box; }
  html, body { width: 1200px; height: 757px; overflow: hidden; }
  body {
    background: var(--backdrop);
    font-family: "Open Sans", Arial, sans-serif;
    color: var(--ink);
    position: relative;
  }
  .card {
    position: absolute;
    width: 513px;
    height: 293px;
    background: var(--card-white);
    box-shadow: var(--card-shadow);
    overflow: hidden;
  }
  .card--contact { left: 335px; top: 54px; }
  .card--logo    { left: 63px;  top: 393px; }
  .card--feature {
    left: 627px; top: 393px;
    background: linear-gradient(135deg, var(--card-grey-light) 0%, var(--card-grey-dark) 100%);
  }

  .brand {
    position: absolute;
    display: flex;
    align-items: center;
    gap: 9px;
    font-weight: 400;
    color: var(--brand-green);
    white-space: nowrap;
    line-height: 1;
  }
  .brand__square { display: block; background: var(--brand-green); }
  .card--contact .brand { left: 37px; top: 60px; font-size: 32px; }
  .card--contact .brand__square { width: 28px; height: 28px; }
  .card--logo .brand { left: 88px; top: 133px; font-size: 33px; }
  .card--logo .brand__square { width: 29px; height: 29px; }
  .card--feature .brand { left: 258px; top: 206px; font-size: 25px; }

  .contact-list {
    position: absolute;
    left: 37px; top: 186px;
    list-style: none;
    font-size: 12.5px;
    color: var(--ink);
  }
  .contact-list li {
    display: flex;
    align-items: center;
    gap: 6px;
    height: 21.5px;
  }
  .contact-list svg { width: 10px; height: 10px; fill: var(--ink-soft); }

  .holder {
    position: absolute;
    left: 340px; top: 184px;
    width: 160px;
    text-align: center;
  }
  .holder__name { font-weight: 700; font-size: 20px; color: var(--ink-soft); line-height: 1.2; }
  .holder__title { font-size: 16px; color: var(--ink-soft); margin-top: 4px; }

  .accent-band {
    position: absolute;
    left: 150px; top: 0;
    width: 68px; height: 100%;
    background: linear-gradient(180deg, var(--brand-green-light) 0%, var(--brand-green) 100%);
  }
</style>
</head>
<body>

  <section class="card card--contact" aria-label="Business card front">
    <div class="brand"><span class="brand__square"></span>Stoneford Builders</div>

    <ul class="contact-list">
      <li>
        <svg viewBox="0 0 10 10" aria-hidden="true"><rect x="2.5" y="0" width="5" height="10" rx="1"/></svg>
        +91 98765 43210
      </li>
      <li>
        <svg viewBox="0 0 10 10" aria-hidden="true"><rect x="2.5" y="0.5" width="5" height="3.5"/><rect x="0" y="4" width="10" height="6" rx="1"/></svg>
        +91 98765 43211
      </li>
      <li>
        <svg viewBox="0 0 10 10" aria-hidden="true"><rect x="0" y="2" width="10" height="6.5"/></svg>
        stoneford@xyzmail.com
      </li>
    </ul>

    <div class="holder">
      <p class="holder__name">Your Name</p>
      <p class="holder__title">Title</p>
    </div>
  </section>

  <section class="card card--logo" aria-label="Business card back">
    <div class="brand"><span class="brand__square"></span>Stoneford Builders</div>
  </section>

  <section class="card card--feature" aria-label="Business card alternate back">
    <div class="accent-band"></div>
    <div class="brand">Stoneford Builders</div>
  </section>

</body>
</html>
```